TALMORK

The business want a professional looking business card. We have a scetch we will add but want the extra upgrade, and would like more suggestions for variations of our business cards.

```html
<!DOCTYPE html>
<html lang="en">
<head>
<meta charset="utf-8">
<title>TALMORK Business Card</title>
<link rel="stylesheet" href="https://fonts.googleapis.com/css2?family=Cinzel:wght@500;600&family=Josefin+Sans:wght@400&family=Source+Sans+3:wght@400;600&display=swap">
<style>
  :root {
    --page: #ffffff;
    --ink: #0f1112;
    --ink-soft: #1b1d1e;
    --gold-light: #f3de8a;
    --gold: #d8b451;
    --gold-mid: #c39b4a;
    --gold-deep: #8b6230;
    --shadow: rgba(0, 0, 0, 0.35);
  }
  * { margin: 0; padding: 0; box-sizing: border-box; }
  html, body { width: 1200px; height: 1200px; overflow: hidden; background: var(--page); }
  .sheet { position: relative; width: 1200px; height: 1200px; }

  .card {
    position: absolute;
    left: 209px;
    width: 789px;
    height: 472px;
    overflow: hidden;
    box-shadow: 4px 5px 6px var(--shadow);
  }
  .card--front { top: 116px; }
  .card--back { top: 621px; }

  .front-surface {
    position: absolute; inset: 0;
    background: linear-gradient(90deg,
      var(--gold-light) 0%, var(--gold-mid) 18%, var(--gold-deep) 32%,
      var(--gold-mid) 50%, var(--gold-light) 78%, var(--gold) 100%);
  }
  .lens { position: absolute; inset: 0; width: 789px; height: 472px; }

  .contact-block { position: absolute; left: 50px; top: 0; font-family: "Source Sans 3", sans-serif; }
  .person-name {
    position: absolute; top: 140px; left: 0; white-space: nowrap;
    font-weight: 600; font-size: 25px; letter-spacing: 0.01em; color: var(--gold-light);
  }
  .person-role {
    position: absolute; top: 178px; left: 0; white-space: nowrap;
    font-weight: 400; font-size: 22px; color: var(--gold);
  }
  .role-rule { position: absolute; top: 219px; left: 0; width: 65px; height: 1.5px; background: var(--gold); }

  .contact-list { position: absolute; top: 258px; left: 0; list-style: none; }
  .contact-item {
    display: flex; align-items: center; height: 38px; white-space: nowrap;
    font-size: 20px; color: var(--gold-light);
  }
  .contact-icon { width: 18px; height: 18px; margin-right: 14px; }

  .company-lockup {
    position: absolute; left: 544px; top: 52px;
    border-left: 2px solid var(--ink); padding-left: 12px;
    font-family: "Cinzel", serif; font-weight: 600; font-size: 30px; line-height: 33px;
    color: var(--ink);
  }

  .brand-front { position: absolute; left: 420px; top: 212px; width: 380px; text-align: center; }
  .brand-mark { display: block; width: 70px; height: 70px; margin: 0 auto 32px; border-radius: 50%; background: var(--ink); }
  .brand-name {
    font-family: "Cinzel", serif; font-weight: 500; font-size: 37px;
    letter-spacing: 0.38em; padding-left: 0.38em; color: var(--ink); line-height: 1;
  }
  .brand-since {
    margin-top: 14px;
    font-family: "Josefin Sans", sans-serif; font-size: 15px;
    letter-spacing: 0.4em; padding-left: 0.4em; color: var(--ink);
  }

  .back-surface {
    position: absolute; inset: 0;
    background: radial-gradient(ellipse at 50% 50%, var(--ink-soft) 0%, var(--ink) 75%);
  }
  .brand-back { position: absolute; left: 0; right: 0; top: 188px; text-align: center; }
  .brand-back .brand-name { font-size: 78px; letter-spacing: 0.28em; padding-left: 0.28em; color: var(--gold); }
  .brand-back .brand-since {
    margin-top: 22px; font-size: 28px; letter-spacing: 0.42em; padding-left: 0.42em; color: var(--gold);
  }
</style>
</head>
<body>
<main class="sheet">

  <section class="card card--front" aria-label="Business card front">
    <div class="front-surface" role="img" aria-label="Metallic gold surface with fine faceted line pattern"></div>

    <svg class="lens" viewBox="0 0 789 472" aria-hidden="true">
      <defs>
        <linearGradient id="ringGold" x1="0" y1="0" x2="1" y2="0">
          <stop offset="0" stop-color="#f0d37a"/>
          <stop offset="0.6" stop-color="#d9b04f"/>
          <stop offset="1" stop-color="#b68a3c"/>
        </linearGradient>
      </defs>
      <path d="M0,40 C170,-10 390,20 500,238 C390,430 180,500 0,456 Z" fill="url(#ringGold)"/>
      <path d="M0,55 C165,8 375,36 482,238 C378,415 175,480 0,440 Z" fill="#0f1112"/>
    </svg>

    <div class="contact-block">
      <h1 class="person-name">ERIK HALVOR BRENNLI</h1>
      <p class="person-role">CEO &amp; Founder</p>
      <span class="role-rule"></span>
      <ul class="contact-list">
        <li class="contact-item">
          <svg class="contact-icon" viewBox="0 0 18 18" aria-hidden="true"><rect x="5" y="1" width="8" height="16" rx="1.5" fill="none" stroke="#d8b451" stroke-width="1.4"/><circle cx="9" cy="14.2" r="0.9" fill="#d8b451"/></svg>
          00 412 345 6789
        </li>
        <li class="contact-item">
          <svg class="contact-icon" viewBox="0 0 18 18" aria-hidden="true"><rect x="1.5" y="4" width="15" height="10" fill="#d8b451"/><path d="M1.5,4 L9,10 L16.5,4" fill="none" stroke="#0f1112" stroke-width="1.2"/></svg>
          talmork.co@mailbox.com
        </li>
        <li class="contact-item">
          <svg class="contact-icon" viewBox="0 0 18 18" aria-hidden="true"><g fill="none" stroke="#d8b451" stroke-width="1.2"><circle cx="9" cy="9" r="7.5"/><ellipse cx="9" cy="9" rx="3.3" ry="7.5"/><path d="M1.5,9 H16.5 M3,5 H15 M3,13 H15"/></g></svg>
          www.talmork.co
        </li>
      </ul>
    </div>

    <div class="company-lockup">TALMORK<br>BRENNLI</div>

    <div class="brand-front">
      <span class="brand-mark"></span>
      <div class="brand-name">TALMORK</div>
      <div class="brand-since">SINCE 2026</div>
    </div>
  </section>

  <section class="card card--back" aria-label="Business card back">
    <div class="back-surface" role="img" aria-label="Black surface with fine gold faceted line pattern"></div>
    <div class="brand-back">
      <div class="brand-name">TALMORK</div>
      <div class="brand-since">SINCE 2026</div>
    </div>
  </section>

</main>
</body>
</html>
```